Corvane Holdings , new business card design

investment firm with corporate clients . need double sided business card , vertical and horizontal options ,logo must be clear. prefer pantone colors only and sharp design. website also www.corvane.ae

Khalid Bin Tarrafi
Managing Director
Tel. +971 4 387 2940
Mobile +971 50 518 2403
khalid@corvane.ae
Q-Span Plaza, officw 18-B07, Warqa Gardens, Dubai

Contact Information for Business Card

Khalid Bin Tarrafi
Managing Director

Font styles to use
Serif

Colors

Designer to choose colors to be used in the design.

```html
<!DOCTYPE html>
<html lang="en">
<head>
<meta charset="utf-8">
<title>Corvane Holdings – Business Card</title>
<link href="https://fonts.googleapis.com/css2?family=Jost:wght@300;400&family=Oswald:wght@500&display=swap" rel="stylesheet">
<style>
  :root {
    --stage: #1a1a1a;
    --card: #262626;
    --card-edge: #2e2e2e;
    --accent: #4a7db5;
    --ink: #f2f2f2;
    --logo-ink: #cfcfcf;
  }
  * { margin: 0; padding: 0; box-sizing: border-box; }
  html, body { width: 1200px; height: 900px; overflow: hidden; background: var(--stage); }
  .canvas {
    width: 1200px; height: 900px;
    display: flex; flex-direction: column; align-items: center; justify-content: center;
    gap: 60px;
    font-family: "Jost", "Futura", sans-serif;
  }
  .card {
    position: relative;
    width: 630px; height: 360px;
    background: radial-gradient(circle at 75% 70%, var(--card-edge), var(--card) 65%);
    border-bottom: 5px solid var(--accent);
    box-shadow: 0 18px 40px rgba(0,0,0,.55);
  }
  /* front */
  .card-front { display: flex; align-items: center; justify-content: center; }
  .brand { display: flex; align-items: center; gap: 18px; }
  .brand-square { width: 22px; height: 22px; background: var(--logo-ink); }
  .brand-name {
    font-weight: 300; font-size: 40px; letter-spacing: 10px;
    color: var(--logo-ink); text-transform: uppercase;
  }
  /* back */
  .identity {
    position: absolute; right: 360px; top: 120px; text-align: right;
  }
  .person-name {
    font-family: "Oswald", "Arial Narrow", sans-serif;
    font-weight: 500; font-size: 30px; color: var(--accent);
    text-transform: uppercase; line-height: 1.1; white-space: nowrap;
  }
  .person-title { font-size: 18px; color: var(--ink); margin-top: 2px; }
  .divider {
    position: absolute; left: 292px; top: 140px;
    width: 2px; height: 70px; background: var(--accent);
  }
  .contacts {
    position: absolute; left: 330px; top: 132px;
    list-style: none; color: var(--ink); font-size: 19px; line-height: 27px;
  }
  .contacts li { display: flex; align-items: center; gap: 14px; }
  .contacts svg { width: 12px; height: 12px; flex: none; }
  .address {
    position: absolute; left: 120px; bottom: 46px;
    color: var(--ink); font-size: 19px; white-space: nowrap;
  }
</style>
</head>
<body>
<main class="canvas">
  <section class="card card-front" aria-label="Card front">
    <div class="brand">
      <span class="brand-square"></span>
      <span class="brand-name">Corvane Holdings</span>
    </div>
  </section>

  <section class="card card-back" aria-label="Card back">
    <div class="identity">
      <h1 class="person-name">Khalid Bin Tarrafi</h1>
      <p class="person-title">Managing Director</p>
    </div>
    <span class="divider"></span>
    <ul class="contacts">
      <li>
        <svg viewBox="0 0 12 12" aria-hidden="true"><path d="M3 1 L5 3 L4 5 Q5 7 7 8 L9 7 L11 9 L9.5 11 Q2 9 1 2.5 Z" fill="var(--accent)"/></svg>
        +971 4 387 2940
      </li>
      <li>
        <svg viewBox="0 0 12 12" aria-hidden="true"><rect x="3" y="0.5" width="6" height="11" rx="1" fill="none" stroke="var(--accent)" stroke-width="1.2"/><circle cx="6" cy="9.5" r=".7" fill="var(--accent)"/></svg>
        +971 50 518 2403
      </li>
      <li>
        <svg viewBox="0 0 12 12" aria-hidden="true"><rect x="0.6" y="2.5" width="10.8" height="7" fill="none" stroke="var(--accent)" stroke-width="1.2"/><path d="M0.6 2.5 L6 6.5 L11.4 2.5" fill="none" stroke="var(--accent)" stroke-width="1.2"/></svg>
        khalid@corvane.ae
      </li>
    </ul>
    <p class="address">Q-Span Plaza, officw 18-B07, Warqa Gardens, Dubai</p>
  </section>
</main>
</body>
</html>
```